Automotive component supplier needs a business card design

We need a business card design for our company called Velran Global Components Ltd based in the UK. We are a supplier of interior and exterior components to premium car manufacturers such as Corvel Ashby, Hadley Fenn, Marquist and Tavarelli. We would like to see a modern business card design that uses the colour blue.

Target Market(s)

Premium automotive car manufacturers.

Industry/Entity Type

Automotive

Contact Information for Business Card

Company Name : Velran Global Components Limited
Address: 17 Marlow Yard, Upper Heath, Warwick, CV31 8QL, United Kingdom
Web Address : www.velrancomponents-example.co.uk

Font styles to use
Other font styles liked:
• Helvetica

Colors
3176b5
0255a3
85acd3
cfdeed
cee9f5
85cae6
34a6d7
0692cd
9bcb3c

Requirements
Must have
• Clear company logo and a mixture of blue colours.
Nice to have
• A high quality modern image.
Should not have
• Multiple colours.

```html
<!DOCTYPE html>
<html lang="en">
<head>
<meta charset="utf-8">
<title>Velran Global Components – Business Card</title>
<link rel="stylesheet" href="https://fonts.googleapis.com/css2?family=Arimo:wght@400;700&display=swap">
<style>
  :root {
    --brand-blue: #0692cd;
    --deep-blue: #0a8bc8;
    --text-blue: #1e8fcf;
    --accent-green: #9bcb3c;
    --card-white: #ffffff;
    --backdrop: #3a3531;
  }
  * { margin: 0; padding: 0; box-sizing: border-box; }
  html, body {
    width: 1200px; height: 780px; overflow: hidden;
    background: var(--backdrop);
    font-family: "Arimo", Helvetica, Arial, sans-serif;
  }
  .canvas { position: relative; width: 1200px; height: 780px; }

  .card {
    position: absolute;
    width: 540px; height: 309px;
    box-shadow: 0 10px 30px rgba(0,0,0,0.45);
    overflow: hidden;
  }

  /* Front */
  .card-front { left: 60px; top: 100px; background: var(--brand-blue); }
  .card-front .brand {
    position: absolute; left: 0; right: 0; top: 104px;
    text-align: center; color: var(--card-white);
  }

  .brand-name {
    display: inline-flex; align-items: flex-start; gap: 6px;
    font-weight: 700; font-size: 62px; letter-spacing: 2px; line-height: 1;
  }
  .brand-dot {
    width: 12px; height: 12px; border-radius: 50%;
    background: var(--accent-green); margin-top: 2px;
  }
  .brand-tagline {
    display: block; margin-top: 6px;
    font-size: 13px; font-weight: 400; letter-spacing: 3.4px;
  }

  /* Back */
  .card-back { left: 600px; top: 380px; background: var(--card-white); }
  .card-back .brand {
    position: absolute; left: 34px; top: 104px; color: var(--brand-blue);
  }
  .card-back .brand-name { font-size: 50px; }
  .card-back .brand-tagline { font-size: 10.5px; letter-spacing: 2.6px; }

  .divider {
    position: absolute; left: 290px; top: 34px;
    width: 1px; height: 170px; background: var(--accent-green); opacity: 0.6;
  }

  .contact {
    position: absolute; left: 306px; top: 38px;
    color: var(--text-blue); font-size: 11.5px; line-height: 1.35;
  }
  .contact .person-name { font-weight: 700; font-size: 15px; letter-spacing: 0.5px; }
  .contact .person-role { color: var(--accent-green); font-size: 12px; margin-bottom: 6px; }
  .contact .address { margin-bottom: 6px; }
  .contact-line { display: flex; align-items: center; gap: 6px; height: 17px; }
  .icon {
    width: 13px; height: 13px; flex: none;
    background: var(--accent-green); border-radius: 2px;
    display: flex; align-items: center; justify-content: center;
  }
  .icon svg { width: 9px; height: 9px; }

  .base-band {
    position: absolute; left: 0; right: 0; bottom: 0; height: 52px;
    background: var(--deep-blue);
    border-top: 3px solid var(--accent-green);
    box-shadow: inset 0 3px 0 var(--card-white);
  }
</style>
</head>
<body>
<main class="canvas">

  <section class="card card-front" aria-label="Card front">
    <div class="brand">
      <span class="brand-name">VELRAN<span class="brand-dot"></span></span>
      <span class="brand-tagline">GLOBAL COMPONENTS</span>
    </div>
  </section>

  <section class="card card-back" aria-label="Card back">
    <div class="brand">
      <span class="brand-name">VELRAN<span class="brand-dot"></span></span>
      <span class="brand-tagline">GLOBAL COMPONENTS</span>
    </div>

    <div class="divider"></div>

    <div class="contact">
      <p class="person-name">EMPLOYEE NAME</p>
      <p class="person-role">Managing Director</p>
      <p class="address">17 Marlow Yard, Upper Heath<br>Warwick, CV31 8QL<br>United Kingdom</p>

      <p class="contact-line">
        <span class="icon"><svg viewBox="0 0 10 10"><rect x="2.5" y="0.5" width="5" height="9" rx="1" fill="#fff"/></svg></span>
        (01) 5550 1842
      </p>
      <p class="contact-line">
        <span class="icon"><svg viewBox="0 0 10 10"><rect x="2.5" y="0.5" width="5" height="3" fill="#fff"/><rect x="0.5" y="3.5" width="9" height="4" fill="#fff"/><rect x="2.5" y="7" width="5" height="2.5" fill="#fff"/></svg></span>
        (01) 5550 1843
      </p>
      <p class="contact-line">
        <span class="icon"><svg viewBox="0 0 10 10"><rect x="0.5" y="2" width="9" height="6" fill="#fff"/><path d="M0.8 2.3 L5 5.5 L9.2 2.3" fill="none" stroke="#9bcb3c" stroke-width="1"/></svg></span>
        info@velran-example.com
      </p>
      <p class="contact-line">
        <span class="icon"><svg viewBox="0 0 10 10"><circle cx="5" cy="5" r="4.2" fill="none" stroke="#fff" stroke-width="1.1"/><ellipse cx="5" cy="5" rx="1.8" ry="4.2" fill="none" stroke="#fff" stroke-width="0.9"/><line x1="0.8" y1="5" x2="9.2" y2="5" stroke="#fff" stroke-width="0.9"/></svg></span>
        www.velrancomponents-example.co.uk
      </p>
    </div>

    <div class="base-band"></div>
  </section>

</main>
</body>
</html>
```